Freelance Translator in Need of a Business Card

I am a freelance Japanese to English translator. I work in the video game localization industry and do literary translation in my spare time. I would like to have both the English word 'Translator' and the Japanese '翻訳者' in the job title. The final design should evoke trust, openness, and reliability.

Target Market(s)

Video game localization companies
Japanese comic book artists

Industry/Entity Type

Business

Contact Information for Business Card

Daniel Forsvik, Translator
dan.forsvik@quellmail.net
torvenwords.com
twitter: @torven_wd

Colors

Designer to choose colors to be used in the design.

```html
<!DOCTYPE html>
<html lang="en">
<head>
<meta charset="UTF-8">
<title>Daniel Forsvik — Translator Business Card</title>
<link rel="stylesheet" href="https://fonts.googleapis.com/css2?family=Tinos:ital,wght@0,400;1,700&family=Lato:wght@400&family=Noto+Sans+JP:wght@400&display=swap">
<style>
  :root {
    --backdrop: #3b3b3b;
    --card: #0c0c0c;
    --ink: #ffffff;
    --ink-soft: #e6e6e6;
  }
  * { margin: 0; padding: 0; box-sizing: border-box; }
  html, body {
    width: 1200px;
    height: 750px;
    overflow: hidden;
    background: var(--backdrop);
  }
  .canvas {
    position: relative;
    width: 1200px;
    height: 750px;
  }
  .card {
    position: absolute;
    left: 366px;
    width: 467px;
    height: 267px;
    background: var(--card);
    color: var(--ink);
    overflow: hidden;
  }
  .card--front { top: 93px; }
  .card--back { top: 406px; }

  /* Front */
  .wordmark {
    position: absolute;
    left: 0;
    right: 0;
    top: 120px;
    display: flex;
    justify-content: center;
    align-items: center;
    gap: 8px;
    font-family: "Tinos", "Times New Roman", serif;
    font-size: 22px;
    letter-spacing: 1px;
    color: var(--ink);
  }
  .wordmark__square {
    width: 12px;
    height: 12px;
    background: var(--ink);
  }

  /* Back */
  .identity {
    position: absolute;
    left: 0;
    right: 0;
    top: 92px;
    text-align: center;
  }
  .identity__name {
    font-family: "Tinos", "Times New Roman", serif;
    font-weight: 400;
    font-size: 21px;
    letter-spacing: 0.5px;
    line-height: 26px;
  }
  .identity__title {
    font-family: "Lato", Arial, sans-serif;
    font-size: 12.5px;
    line-height: 18px;
    color: var(--ink-soft);
  }
  .identity__title-jp {
    font-family: "Noto Sans JP", sans-serif;
    margin-left: 9px;
  }
  .contacts {
    position: absolute;
    left: 0;
    right: 0;
    top: 150px;
    text-align: center;
    list-style: none;
    font-family: "Lato", Arial, sans-serif;
    font-size: 12px;
    line-height: 16px;
    color: var(--ink-soft);
  }
  .contacts__label {
    font-family: "Tinos", "Times New Roman", serif;
    font-style: italic;
    font-weight: 700;
  }
  .divider {
    position: absolute;
    left: 0;
    top: 240px;
    width: 467px;
    height: 12px;
  }
</style>
</head>
<body>
<main class="canvas">
  <section class="card card--front" aria-label="Business card front">
    <div class="wordmark">
      <span class="wordmark__name">DANIEL FORSVIK</span>
      <span class="wordmark__square" aria-hidden="true"></span>
    </div>
  </section>

  <section class="card card--back" aria-label="Business card back">
    <div class="identity">
      <h1 class="identity__name">DANIEL FORSVIK</h1>
      <p class="identity__title">Translator<span class="identity__title-jp" lang="ja">翻訳者</span></p>
    </div>
    <ul class="contacts">
      <li><span class="contacts__label">email:</span> dan.forsvik@quellmail.net</li>
      <li><span class="contacts__label">web:</span> torvenwords.com</li>
      <li><span class="contacts__label">twitter:</span> @torven_wd</li>
    </ul>
    <svg class="divider" viewBox="0 0 467 12" aria-hidden="true">
      <line x1="0" y1="6" x2="191" y2="6" stroke="#ffffff" stroke-width="1"/>
      <circle cx="200" cy="6" r="1.5" fill="#ffffff"/>
      <circle cx="216" cy="6" r="1.5" fill="#ffffff"/>
      <circle cx="232" cy="6" r="1.5" fill="#ffffff"/>
      <circle cx="248" cy="6" r="1.5" fill="#ffffff"/>
      <circle cx="264" cy="6" r="1.5" fill="#ffffff"/>
      <line x1="275" y1="6" x2="467" y2="6" stroke="#ffffff" stroke-width="1"/>
    </svg>
  </section>
</main>
</body>
</html>
```